Business card design for Automotive workshop

We need a business card for a new automotive repair and tyre shop called Keelstone Prime Automotive located in New Zealand. We are a clean, modern and fresh workshop and company.

Front needs to feature logo,
my name:
Marlo Fenwicke (director)

Address:
48 Tarn Lane
Marewa Bay 3582

Phone: 07 594 2713
Mobile: 027 451 9362
Email: office@keelstoneautomotive.example.nz
Website: keelstoneautomotive.example.nz

Back needs to feature an area to write down appointment details, date and time.

Also feature a list of jobs and work we do such as,
Vehicle Servicing
All Mechanical Repairs
Warrant of Fitness
Tyres & Wheel Alignments
Automotive Diagnostics
Automotive Parts & Supplies

```html
<!DOCTYPE html>
<html lang="en">
<head>
<meta charset="utf-8">
<title>Keelstone Prime Automotive – Business Card</title>
<link rel="stylesheet" href="https://fonts.googleapis.com/css2?family=Montserrat:wght@400;500;700;800&display=swap">
<style>
  :root {
    --bg: #d8d8d5;
    --card: #111111;
    --band: #333333;
    --red: #e3161f;
    --white: #ffffff;
    --muted: #bdbdbd;
  }
  * { box-sizing: border-box; margin: 0; padding: 0; }
  html, body { width: 1200px; height: 801px; overflow: hidden; }
  body {
    background: var(--bg);
    font-family: "Montserrat", sans-serif;
    display: flex;
    align-items: center;
    justify-content: center;
    gap: 30px;
  }
  .card {
    position: relative;
    width: 560px;
    height: 320px;
    background: var(--card);
    color: var(--white);
    border-bottom: 4px solid var(--red);
    box-shadow: 0 10px 24px rgba(0,0,0,.25);
    overflow: hidden;
  }

  /* Front */
  .brand {
    position: absolute;
    top: 62px; left: 0; right: 0;
    display: flex; align-items: center; justify-content: center; gap: 12px;
  }
  .brand-mark { width: 16px; height: 16px; background: var(--red); }
  .brand-name {
    font-weight: 800; font-size: 26px; letter-spacing: 1px;
    text-transform: uppercase; color: var(--red); white-space: nowrap;
  }
  .front-info {
    position: absolute;
    top: 160px; left: 0; right: 0;
    display: flex; justify-content: center; gap: 22px;
  }
  .person { text-align: right; padding-top: 6px; }
  .person-name { color: var(--red); font-weight: 700; font-size: 19px; margin-bottom: 4px; }
  .person-role, .address { font-size: 12.5px; line-height: 1.45; }
  .divider { width: 1px; background: #777; }
  .contacts { list-style: none; font-size: 12px; line-height: 1.6; padding-top: 4px; }
  .contacts li { display: flex; align-items: center; gap: 8px; white-space: nowrap; }
  .contacts svg { width: 10px; height: 10px; fill: var(--red); flex: none; }

  /* Back */
  .appointment-title {
    position: absolute; top: 46px; left: 0; right: 0;
    text-align: center; color: var(--red); font-weight: 700; font-size: 22px;
  }
  .appointment-band {
    position: absolute;
    top: 80px; left: 0; right: 0; height: 105px;
    background: var(--band);
  }
  .fields {
    position: absolute; top: 196px; left: 30px; right: 30px;
    display: flex; gap: 24px;
  }
  .field { flex: 1; display: flex; align-items: flex-end; gap: 8px; font-weight: 700; font-size: 16px; }
  .field-line { flex: 1; border-bottom: 1px dashed var(--muted); margin-bottom: 4px; }
  .works-heading {
    position: absolute; top: 236px; left: 60px; right: 60px;
    display: flex; align-items: center; gap: 12px;
    font-weight: 700; font-size: 14px; white-space: nowrap;
  }
  .works-heading::before, .works-heading::after { content: ""; flex: 1; height: 1px; background: var(--red); }
  .works-list {
    position: absolute; top: 262px; left: 20px; right: 20px;
    list-style: none; display: flex; flex-wrap: wrap; justify-content: center;
    column-gap: 16px; row-gap: 6px; font-size: 11.5px;
  }
  .works-list li { display: flex; align-items: center; gap: 5px; white-space: nowrap; }
  .works-list li::before { content: ""; width: 5px; height: 5px; border-radius: 50%; background: var(--red); }
</style>
</head>
<body>

<section class="card card-front">
  <div class="brand">
    <span class="brand-mark"></span>
    <span class="brand-name">Keelstone Prime Automotive</span>
  </div>
  <div class="front-info">
    <div class="person">
      <p class="person-name">Marlo Fenwicke</p>
      <p class="person-role">Director</p>
      <p class="address">48 Tarn Lane<br>Marewa Bay 3582</p>
    </div>
    <div class="divider"></div>
    <ul class="contacts">
      <li><svg viewBox="0 0 10 10"><path d="M2 0l2 2.5-1 1.2a6 6 0 0 0 3.3 3.3l1.2-1L10 8l-1.3 2C4 10 0 6 0 1.3z"/></svg>07 594 2713</li>
      <li><svg viewBox="0 0 10 10"><path d="M2.5 0h5v10h-5zM3.3 1v7h3.4V1z"/></svg>027 451 9362</li>
      <li><svg viewBox="0 0 10 10"><path d="M0 2h10v6H0zM1 3l4 3 4-3"/></svg>office@keelstoneautomotive.example.nz</li>
      <li><svg viewBox="0 0 10 10"><circle cx="5" cy="5" r="5"/></svg>keelstoneautomotive.example.nz</li>
    </ul>
  </div>
</section>

<section class="card card-back">
  <div class="appointment-band"></div>
  <h2 class="appointment-title">Appointment Details</h2>
  <div class="fields">
    <div class="field">Date <span class="field-line"></span></div>
    <div class="field">Time <span class="field-line"></span></div>
  </div>
  <h3 class="works-heading">Our Works</h3>
  <ul class="works-list">
    <li>Vehicle Servicing</li>
    <li>Warrant of Fitness</li>
    <li>Automotive Parts &amp; Supplies</li>
    <li>Automotive Diagnostics</li>
    <li>Tyres &amp; Wheel Alignments</li>
    <li>All Mechanical Repairs</li>
  </ul>
</section>

</body>
</html>
```